Fahrzeugbeschriftung
Zielgruppe
Gefällt mir selbst
Aufgabenstellung
Das Motto ist 'Comet Lady 4.1' auf einer Anhängerseite L 4 m x H 2,05 m.
Seite rechts, die mit Tür. Es handelt sich um den folgenden Anhänger KORVEX R5830QM Sandwich 400 x200x205 cm
Mein Logo muss ohne !! Namen verwendet werden.
Hinweis auf meinen Instagram Account @lindnertamia ist zwingend einzubauen
Ja, wie könnte Comet Lady 4.1 heute aussehen, was würde sie tun? Muss es ein Bild sein? Reicht vielleicht auch ein Schriftzug?
Ich selbst lese, schreibe Blog und Bücher, stricke, schwimme, organisiere Veranstaltungen für Frauen, coache Freundinnen und andere Frauen ehrenamtlich. Stehe für Gleichberechtigung. Bin Feministin durch und durch. Aber bin ich auch 'Comet Lady 4.1'?
Wie stellen Sie sich 'Comet Lady 4.1' als Anhänger-Design vor? Überraschen Sie mich!
Hier meine Website www.moos-lindner.de
Keine Fotos von mir verwenden.
Regenbogen? Schließlich wurde das originale comet Lady von einem Mann für Frauen 'erfunden'

```html
<!DOCTYPE html>
<html lang="de">
<head>
<meta charset="utf-8">
<title>Comet Lady 4.1 – Anhängerseite</title>
<link rel="stylesheet" href="https://fonts.googleapis.com/css2?family=Kanit:wght@500&family=Montserrat:wght@500;800;900&display=swap">
<style>
  :root {
    --page-bg: #ffffff;
    --panel-bg: #ffffff;
    --pattern-tone: #eeeef2;
    --pattern-edge: #d9d9de;
    --brand-red: #9b0d1e;
    --ink: #151515;
    --wave-violet: #6b4cf0;
    --wave-purple: #8a3cf0;
    --wave-magenta: #d63fd6;
    --wave-orange: #f0a21a;
    --wave-peach: #f7c79a;
  }
  * { box-sizing: border-box; margin: 0; padding: 0; }
  html, body {
    width: 1200px;
    height: 1083px;
    overflow: hidden;
    background: var(--page-bg);
  }
  .canvas {
    position: relative;
    width: 1200px;
    height: 1083px;
    background: var(--page-bg);
  }

  /* Trailer side panel, shown flat */
  .trailer-side {
    position: absolute;
    left: 40px;
    top: 60px;
    width: 1120px;
    height: 640px;
    background: var(--panel-bg);
    border: 1px solid var(--pattern-edge);
    overflow: hidden;
  }
  .line-art-field {
    position: absolute;
    inset: 0;
    background: linear-gradient(160deg, #f6f6f8 0%, var(--pattern-tone) 55%, #f4f4f7 100%);
  }

  .insta-handle {
    position: absolute;
    left: 70px;
    top: 62px;
    display: flex;
    align-items: center;
    gap: 12px;
    font-family: "Kanit", sans-serif;
    font-weight: 500;
    font-size: 38px;
    color: var(--ink);
  }
  .insta-handle .dot {
    width: 40px;
    height: 40px;
    border-radius: 50%;
    background: var(--brand-red);
    flex: none;
  }

  .brand-tile {
    position: absolute;
    right: 150px;
    top: 0;
    width: 150px;
    height: 150px;
    background: var(--brand-red);
    display: flex;
    align-items: center;
    justify-content: center;
    text-align: center;
    padding: 12px;
    font-family: "Montserrat", sans-serif;
    font-weight: 500;
    font-size: 15px;
    line-height: 1.3;
    color: #ffffff;
  }

  .motto {
    position: absolute;
    left: 0;
    right: 0;
    top: 190px;
    text-align: center;
    font-family: "Montserrat", sans-serif;
    font-weight: 900;
    line-height: 0.98;
    letter-spacing: -1px;
    text-transform: uppercase;
  }
  .motto .line {
    display: block;
    font-size: 118px;
  }
  .motto .wave-text {
    background: linear-gradient(180deg,
      var(--wave-violet) 0%,
      var(--wave-purple) 30%,
      var(--wave-magenta) 48%,
      var(--wave-orange) 66%,
      var(--wave-peach) 100%);
    -webkit-background-clip: text;
    background-clip: text;
    color: transparent;
  }
  .motto .version {
    color: var(--brand-red);
    font-weight: 800;
    margin-left: 10px;
  }

  .web-address {
    position: absolute;
    left: 0;
    right: 0;
    top: 470px;
    text-align: center;
    font-family: "Montserrat", sans-serif;
    font-weight: 500;
    font-size: 42px;
    color: var(--ink);
  }

  /* Brand block below */
  .brand-block {
    position: absolute;
    left: 0;
    right: 0;
    top: 800px;
    height: 220px;
    display: flex;
    flex-direction: column;
    align-items: center;
    justify-content: center;
    gap: 22px;
  }
  .brand-block .mark {
    width: 70px;
    height: 70px;
    border-radius: 50%;
    border: 3px solid var(--brand-red);
  }
  .brand-block .name {
    font-family: "Montserrat", sans-serif;
    font-weight: 500;
    font-size: 34px;
    color: var(--brand-red);
  }
</style>
</head>
<body>
  <main class="canvas">
    <section class="trailer-side">
      <div class="line-art-field" role="img" aria-label="Feines graues Linienmuster aus gezeichneten Frauenporträts als Hintergrund"></div>

      <div class="insta-handle">
        <span class="dot"></span>
        <span>@lindnertamia</span>
      </div>

      <div class="brand-tile">Tina Moos-Lindner</div>

      <h1 class="motto">
        <span class="line wave-text">Comet</span>
        <span class="line"><span class="wave-text">Lady</span><span class="version">4.1</span></span>
      </h1>

      <p class="web-address">www.moos-lindner.de</p>
    </section>

    <section class="brand-block">
      <span class="mark"></span>
      <span class="name">Tina Moos-Lindner</span>
    </section>
  </main>
</body>
</html>
```